Home Security Company Business Card

Looking for a eye catching business card that is non traditional and stands out but yet still looks professional. It should include all the pertinent information such as name, title, address, telephone, e-mail, website address should definitely stand out and then finally the logo.

Target Market(s)

Residential and Commercial accounts mostly upscale accounts

Industry/Entity Type

Security

Contact Information for Business Card

Name
Title
Address
Office #
Cell #
E-mail
Website

Font styles to use
Serif
Sans Serif

Requirements
Must have
• Logo, two sided color configuration
Nice to have
• You decide
Should not have
• There really aren't any.

```html
<!DOCTYPE html>
<html lang="en">
<head>
<meta charset="utf-8">
<title>Bulwark Protection Group – Business Card</title>
<link rel="stylesheet" href="https://fonts.googleapis.com/css2?family=Source+Sans+3:wght@400;600&display=swap">
<style>
  :root {
    --backdrop: #141414;
    --card-white: #ffffff;
    --brand-red: #7b1514;
    --deep-red: #6e1211;
    --gold-light: #f3c25e;
    --gold-mid: #c9712a;
    --text-grey: #555555;
  }
  html, body {
    margin: 0;
    width: 1200px;
    height: 900px;
    overflow: hidden;
    background: var(--backdrop);
    font-family: "Source Sans 3", "Myriad Pro", Arial, sans-serif;
  }
  .canvas {
    position: relative;
    width: 1200px;
    height: 900px;
  }
  .card {
    position: absolute;
    top: 170px;
    width: 347px;
    height: 561px;
    box-shadow: 0 4px 14px rgba(0,0,0,0.55);
    overflow: hidden;
  }
  .card-front {
    left: 259px;
    background: var(--card-white);
  }
  .card-back {
    left: 631px;
    background: radial-gradient(ellipse 60% 50% at 50% 45%, var(--gold-light) 0%, var(--gold-mid) 40%, var(--deep-red) 100%);
  }
  .tab {
    position: absolute;
    left: 102px;
    width: 143px;
    background: var(--brand-red);
  }
  .tab-top { top: 0; height: 30px; }
  .tab-bottom { bottom: 0; height: 28px; }

  .brand {
    position: absolute;
    top: 134px;
    left: 0;
    width: 100%;
    display: flex;
    align-items: center;
    justify-content: center;
    gap: 10px;
  }
  .brand-mark {
    width: 22px;
    height: 22px;
    border-radius: 50%;
    background: var(--brand-red);
  }
  .brand-name {
    font-weight: 600;
    font-size: 19px;
    color: var(--brand-red);
    letter-spacing: 0.2px;
  }

  .details {
    position: absolute;
    top: 278px;
    left: 0;
    width: 100%;
    text-align: center;
    color: var(--text-grey);
    font-size: 15.5px;
    line-height: 20px;
  }
  .person-name {
    margin: 0;
    font-size: 20px;
    line-height: 24px;
    font-weight: 600;
    color: var(--brand-red);
    letter-spacing: 0.3px;
  }
  .person-title { margin: 0; }
  .address { margin: 17px 0 0; }
  .contacts {
    list-style: none;
    margin: 18px 0 0;
    padding: 0;
  }
  .contacts li {
    display: flex;
    align-items: center;
    justify-content: center;
    gap: 6px;
  }
  .contacts svg {
    width: 11px;
    height: 11px;
    fill: var(--brand-red);
    stroke: var(--brand-red);
  }

  .back-name {
    position: absolute;
    top: 0;
    left: 0;
    width: 100%;
    height: 100%;
    display: flex;
    align-items: center;
    justify-content: center;
    font-weight: 600;
    font-size: 24px;
    color: var(--card-white);
    letter-spacing: 0.5px;
  }
</style>
</head>
<body>
<div class="canvas">

  <section class="card card-front">
    <div class="tab tab-top"></div>

    <div class="brand">
      <span class="brand-mark"></span>
      <span class="brand-name">Bulwark Protection Group Inc.</span>
    </div>

    <div class="details">
      <h1 class="person-name">DANIEL HARROW</h1>
      <p class="person-title">Managing Director</p>
      <p class="address">48 Harbour Street, Suite 5<br>Northfield, 204418.</p>
      <ul class="contacts">
        <li>
          <svg viewBox="0 0 12 12" aria-hidden="true"><path stroke="none" d="M1 4 C1 2 3 1 6 1 C9 1 11 2 11 4 L9 5 L8 3.5 L4 3.5 L3 5 Z M3 6 L9 6 L10 11 L2 11 Z"/></svg>
          044-321 654 987
        </li>
        <li>
          <svg viewBox="0 0 12 12" aria-hidden="true"><rect x="3" y="0.5" width="6" height="11" rx="1" stroke="none"/><rect x="4" y="2" width="4" height="6.5" fill="#fff" stroke="none"/></svg>
          044-321 654 987
        </li>
        <li>
          <svg viewBox="0 0 12 12" aria-hidden="true"><rect x="0.5" y="2.5" width="11" height="7" stroke="none"/><path d="M0.8 3 L6 7 L11.2 3" fill="none" stroke="#fff" stroke-width="1"/></svg>
          hello@bulwarkgroup.com
        </li>
        <li>
          <svg viewBox="0 0 12 12" aria-hidden="true"><path d="M5 7 L7 5 M4.5 5 L2.5 7 A1.6 1.6 0 0 0 5 9.5 L7 7.5 M7.5 7 L9.5 5 A1.6 1.6 0 0 0 7 2.5 L5 4.5" fill="none" stroke-width="1.4" stroke-linecap="round"/></svg>
          www.bulwarkgroup.com
        </li>
      </ul>
    </div>

    <div class="tab tab-bottom"></div>
  </section>

  <section class="card card-back" role="img" aria-label="Company emblem area on a warm gold and red glow">
    <div class="back-name">Bulwark Protection Group</div>
  </section>

</div>
</body>
</html>
```